Birchline Septic Solutions

Would like to see some single sided ones but would also like to see some double sided with one sided only being the logo. Owners name is Colin Vandro. Phone number is 555-214-0387
Services are pumping, inspections, installs, and repairs

Contact Information for Business Card

555-241-0387 Colin Vandro Ashford Glen, OH

```html
<!DOCTYPE html>
<html lang="en">
<head>
<meta charset="utf-8">
<title>Birchline Septic Solutions – Business Cards</title>
<link rel="stylesheet" href="https://fonts.googleapis.com/css2?family=Montserrat:wght@500;600;800&display=swap">
<style>
  :root {
    --backdrop: #5d5d62;
    --card-white: #ffffff;
    --card-black: #111112;
    --ink: #1b1b1b;
    --teal: #3dbdb5;
    --muted: #555555;
    --gloss: #2a2a2c;
  }
  * { box-sizing: border-box; margin: 0; padding: 0; }
  html, body {
    width: 1200px; height: 876px; overflow: hidden;
    background: var(--backdrop);
    font-family: "Montserrat", Arial, sans-serif;
  }
  .canvas {
    width: 1200px; height: 876px;
    display: flex; align-items: center; justify-content: center; gap: 40px;
  }
  .card {
    width: 540px; height: 309px;
    border-radius: 4px;
    position: relative;
    box-shadow: 0 14px 30px rgba(0,0,0,.35);
  }

  /* Front */
  .card--front { background: var(--card-white); color: var(--ink); }
  .contact { position: absolute; left: 40px; top: 40px; }
  .contact__name {
    color: var(--teal); font-weight: 800; font-size: 26px;
    letter-spacing: 1px; text-transform: uppercase; line-height: 1;
  }
  .contact__role { font-size: 12px; font-weight: 500; margin: 6px 0 14px; color: var(--ink); }
  .contact__line {
    display: flex; align-items: center; gap: 8px;
    font-size: 15px; font-weight: 500; margin-bottom: 6px; letter-spacing: .5px;
  }
  .contact__line svg { width: 13px; height: 13px; fill: var(--teal); flex: none; }

  .brand {
    position: absolute; right: 40px; top: 118px;
    display: flex; align-items: center; gap: 10px;
    font-weight: 800; font-size: 19px; color: var(--ink);
    text-transform: uppercase; letter-spacing: .5px; line-height: 1.15;
  }
  .brand__square { width: 14px; height: 14px; background: var(--teal); flex: none; }

  .services {
    position: absolute; left: 40px; right: 40px; bottom: 34px;
    font-size: 16px; font-weight: 600; letter-spacing: 1px;
    text-transform: uppercase; white-space: nowrap;
  }
  .services__sep { color: var(--teal); margin: 0 7px; }

  /* Back */
  .card--back {
    background: linear-gradient(110deg, var(--card-black) 0%, var(--card-black) 55%, var(--gloss) 62%, var(--card-black) 75%);
    display: flex; align-items: center; justify-content: center;
  }
  .brand--back {
    position: static; color: #2e2e30; font-size: 28px; gap: 14px;
  }
  .brand--back .brand__square { width: 20px; height: 20px; }
</style>
</head>
<body>
<main class="canvas">
  <section class="card card--front" aria-label="Business card front">
    <div class="contact">
      <h1 class="contact__name">Colin Vandro</h1>
      <p class="contact__role">Owner</p>
      <p class="contact__line">
        <svg viewBox="0 0 24 24" aria-hidden="true"><path d="M6.6 10.8a15.1 15.1 0 0 0 6.6 6.6l2.2-2.2a1 1 0 0 1 1-.25 11.4 11.4 0 0 0 3.6.57 1 1 0 0 1 1 1V20a1 1 0 0 1-1 1A17 17 0 0 1 3 4a1 1 0 0 1 1-1h3.5a1 1 0 0 1 1 1c0 1.25.2 2.45.57 3.57a1 1 0 0 1-.25 1z"/></svg>
        555-214-0387
      </p>
      <p class="contact__line">
        <svg viewBox="0 0 24 24" aria-hidden="true"><path d="M12 2a7 7 0 0 0-7 7c0 5.25 7 13 7 13s7-7.75 7-13a7 7 0 0 0-7-7zm0 9.5A2.5 2.5 0 1 1 12 6.5a2.5 2.5 0 0 1 0 5z"/></svg>
        Ashford Glen, OH
      </p>
    </div>

    <div class="brand">
      <span class="brand__square" aria-hidden="true"></span>
      <span>Birchline<br>Septic Solutions</span>
    </div>

    <p class="services">
      Pumping<span class="services__sep">|</span>Inspections<span class="services__sep">|</span>Installs<span class="services__sep">|</span>Repairs
    </p>
  </section>

  <section class="card card--back" aria-label="Business card back">
    <div class="brand brand--back">
      <span class="brand__square" aria-hidden="true"></span>
      <span>Birchline<br>Septic Solutions</span>
    </div>
  </section>
</main>
</body>
</html>
```